Small Business Broker Business Card Design

A business card design for a small business brokerage, which is a financial service, not unlike real estate brokerage, but for small businesses such as laundromats, pizza shops, restaurants, cleaners etc. The designs should all be simple, more conservative in nature, using the colors and font of the logo. Again, think real estate Brokerage as a business context
Contact Information for Business Card
Name: Glen R. Harlow. Title: Small Business Advisor. Email: g.harlow@bayfieldcapitalworks.example. Mobile: (555) 274-3918. Office: (555) 806-2147. www.bayfieldcapitalworks.example

```html
<!DOCTYPE html>
<html lang="en">
<head>
<meta charset="utf-8">
<title>Bayfield Capital Works – Business Card</title>
<link rel="stylesheet" href="https://fonts.googleapis.com/css2?family=Montserrat:wght@400;500;700;800&display=swap">
<style>
  :root {
    --navy: #1b3a6b;
    --green: #8cc63f;
    --white: #ffffff;
    --ink: #2b2b2b;
    --stage: #202020;
  }
  * { margin: 0; padding: 0; box-sizing: border-box; }
  html, body { width: 1200px; height: 988px; overflow: hidden; background: var(--stage); }
  body { font-family: "Montserrat", sans-serif; position: relative; }

  .card {
    position: absolute;
    left: 220px;
    width: 760px;
    height: 434px;
    border-radius: 26px;
    overflow: hidden;
  }
  .card--back { top: 40px; background: var(--navy); }
  .card--front { top: 514px; background: var(--white); }

  .brand {
    position: absolute;
    display: flex;
    align-items: center;
    gap: 16px;
    font-weight: 800;
    letter-spacing: 0.04em;
    text-transform: uppercase;
    line-height: 1.15;
  }
  .brand__mark { flex: none; background: var(--green); }
  .card--back .brand {
    left: 0; right: 0; top: 0; bottom: 0;
    justify-content: center;
    color: var(--white);
    font-size: 34px;
  }
  .card--back .brand__mark { width: 34px; height: 34px; }
  .card--front .brand {
    left: 44px; top: 170px; width: 300px;
    color: var(--navy);
    font-size: 22px;
  }
  .card--front .brand__mark { width: 22px; height: 22px; }

  .divider {
    position: absolute;
    left: 372px; top: 60px;
    width: 1.5px; height: 300px;
    background: var(--navy);
  }

  .contact { position: absolute; left: 398px; top: 52px; width: 345px; color: var(--ink); }
  .contact__name {
    font-weight: 800;
    font-size: 30px;
    text-transform: uppercase;
    color: var(--navy);
    line-height: 1;
  }
  .contact__name span { color: var(--green); }
  .contact__title { font-size: 15px; margin-top: 6px; }
  .contact__address { font-size: 15px; line-height: 1.45; margin-top: 18px; }
  .contact__list { list-style: none; margin-top: 20px; font-size: 14px; }
  .contact__list li { display: flex; align-items: center; gap: 10px; height: 27px; white-space: nowrap; }
  .contact__list svg { width: 15px; height: 15px; flex: none; }

  .band { position: absolute; left: 0; bottom: 0; width: 760px; height: 22px; }
</style>
</head>
<body>
  <section class="card card--back">
    <div class="brand"><span class="brand__mark"></span>Bayfield Capital Works, Inc</div>
  </section>

  <section class="card card--front">
    <div class="brand"><span class="brand__mark"></span>Bayfield Capital<br>Works, Inc</div>

    <div class="divider"></div>

    <div class="contact">
      <p class="contact__name">Glen <span>R. Harlow</span></p>
      <p class="contact__title">Small Business Advisor</p>
      <p class="contact__address">P.O. Box 214 Harbor Lane<br>Bayfield Falls ON, K7R 3M4</p>
      <ul class="contact__list">
        <li>
          <svg viewBox="0 0 16 16" aria-hidden="true"><path fill="#8cc63f" d="M2 6c0-2 2-3 6-3s6 1 6 3l-2 1-1-2H5L4 7zM4 8h8l1 5H3z"/></svg>
          (555) 806-2147
        </li>
        <li>
          <svg viewBox="0 0 16 16" aria-hidden="true"><rect x="4.5" y="1.5" width="7" height="13" rx="1.5" fill="none" stroke="#8cc63f" stroke-width="1.6"/><circle cx="8" cy="12" r="0.9" fill="#8cc63f"/></svg>
          (555) 274-3918
        </li>
        <li>
          <svg viewBox="0 0 16 16" aria-hidden="true"><rect x="1.5" y="3.5" width="13" height="9" fill="none" stroke="#8cc63f" stroke-width="1.6"/><path d="M1.5 3.5 8 9l6.5-5.5" fill="none" stroke="#8cc63f" stroke-width="1.6"/></svg>
          g.harlow@bayfieldcapitalworks.example
        </li>
        <li>
          <svg viewBox="0 0 16 16" aria-hidden="true"><circle cx="8" cy="8" r="6.5" fill="none" stroke="#8cc63f" stroke-width="1.6"/><path d="M1.5 8h13M8 1.5c-3 3.5-3 9.5 0 13M8 1.5c3 3.5 3 9.5 0 13" fill="none" stroke="#8cc63f" stroke-width="1.2"/></svg>
          www.bayfieldcapitalworks.example
        </li>
      </ul>
    </div>

    <svg class="band" viewBox="0 0 760 22" preserveAspectRatio="none" aria-hidden="true">
      <polygon points="0,0 520,0 500,22 0,22" fill="var(--navy)"/>
      <polygon points="530,0 760,0 760,22 510,22" fill="var(--green)"/>
    </svg>
  </section>
</body>
</html>
```